Maple Roster Business Card for recruitment company

We are looking for a Business Card Design that incorporates our personal details and our busines name and logo. We are a specialized search consultancy that recruit Property and Construction professionals.
We would like a business card that stands out and is appealing to the Construction and Property industry as well.

Target Market(s)

people in the construction and property industry

Contact Information for Business Card

Business Name and logo

Font styles to use
Serif

Colors
0094D4
00A9DD
6FCCEA
C7EBF8
E9F6FB

Requirements
Must have
• Business name and logo as well as contact details
Should not have
• No photos of us please

```html
<!DOCTYPE html>
<html lang="en">
<head>
<meta charset="utf-8">
<title>Maple Roster Business Card</title>
<link rel="stylesheet" href="https://fonts.googleapis.com/css2?family=Lora:wght@400;600&display=swap">
<style>
  :root {
    --backdrop: #d2d2d2;
    --paper: #ffffff;
    --blue-strong: #0094d4;
    --blue-bright: #00a9dd;
    --blue-soft: #6fccea;
    --blue-pale: #c7ebf8;
    --blue-mist: #e9f6fb;
    --ink-body: #2b3a42;
    --ink-muted: #5a6a72;
  }
  * { margin: 0; padding: 0; box-sizing: border-box; }
  html, body { width: 900px; height: 1200px; overflow: hidden; }
  body {
    background: var(--backdrop);
    font-family: "Lora", Georgia, serif;
    position: relative;
  }
  .card {
    position: absolute;
    left: 79px;
    width: 743px;
    height: 441px;
    box-shadow: 0 6px 14px rgba(0,0,0,0.28);
    overflow: hidden;
  }
  .card-front { top: 131px; background: var(--paper); }
  .card-back { top: 638px; height: 440px; background: var(--blue-strong); }

  .brand-name {
    position: absolute;
    font-weight: 400;
    text-transform: uppercase;
    white-space: nowrap;
    line-height: 1;
  }
  .card-front .brand-name {
    left: 57px; top: 202px;
    width: 334px;
    text-align: center;
    font-size: 37px;
    letter-spacing: 2px;
    color: var(--blue-strong);
  }
  .card-back .brand-name {
    left: 0; right: 0; top: 192px;
    text-align: center;
    font-size: 60px;
    letter-spacing: 4px;
    color: var(--paper);
  }

  .divider {
    position: absolute;
    left: 430px; top: 124px;
    width: 1px; height: 195px;
    background: var(--blue-soft);
  }
  .contact-block {
    position: absolute;
    left: 460px; top: 114px;
    color: var(--ink-body);
  }
  .person-name {
    font-size: 25px; font-weight: 600;
    color: var(--blue-strong);
    line-height: 1.2;
  }
  .person-role {
    font-size: 16px; color: var(--ink-muted);
    margin-top: 2px;
  }
  .contact-list { list-style: none; margin-top: 24px; }
  .contact-list li {
    display: flex; align-items: center;
    font-size: 16px; height: 24.5px;
  }
  .contact-list svg { width: 14px; height: 14px; margin-right: 16px; fill: var(--blue-bright); flex: none; }
  .address { margin-top: 18px; font-size: 16px; line-height: 21px; }

  .footer-bands {
    position: absolute; left: 0; bottom: 0;
    width: 743px; height: 46px; display: block;
  }
</style>
</head>
<body>
  <section class="card card-front">
    <div class="brand-name">Maple Roster</div>
    <div class="divider"></div>
    <div class="contact-block">
      <div class="person-name">Dana Whitlow</div>
      <div class="person-role">Owner/ Designer</div>
      <ul class="contact-list">
        <li>
          <svg viewBox="0 0 16 16" aria-hidden="true"><path d="M2 5c0-2 2-3 6-3s6 1 6 3v1h-3V5H5v1H2z"/><path d="M4 7h8l2 6H2z"/></svg>
          (555) 014-2276
        </li>
        <li>
          <svg viewBox="0 0 16 16" aria-hidden="true"><path d="M1 4h14v1L8 9 1 5z"/><path d="M1 6.5l7 4 7-4V13H1z"/></svg>
          info@mapleroster.com
        </li>
        <li>
          <svg viewBox="0 0 16 16" aria-hidden="true"><circle cx="8" cy="8" r="7"/><path d="M5 4c2 0 2 2 4 2s0 3-2 3-1 3-3 2 0-3-2-4z" fill="#fff"/></svg>
          www.mapleroster.com
        </li>
      </ul>
      <div class="address">208 Linden Row<br>Harbor Falls, CA 90412</div>
    </div>
    <svg class="footer-bands" viewBox="0 0 743 46" aria-hidden="true">
      <rect width="743" height="46" fill="var(--blue-strong)"/>
      <path d="M0 0H512C488 0 484 31 452 31H0Z" fill="var(--paper)"/>
      <path d="M0 0H482C470 8 462 23 438 23H0Z" fill="var(--blue-soft)"/>
    </svg>
  </section>

  <section class="card card-back">
    <div class="brand-name">Maple Roster</div>
  </section>
</body>
</html>
```